New website for concierge mobile medical service

new website for business:
WEBSITE REQUEST LIST:
Luxury product look.
Professional. Clean & simple, NO stock people photos. Graphics OK.
Black and white text.

```html
<!DOCTYPE html>
<html lang="en">
<head>
<meta charset="utf-8">
<title>Vela Health – Other</title>
<link rel="stylesheet" href="https://fonts.googleapis.com/css2?family=Fira+Sans:wght@500;600;700&family=Lato:wght@400;700&display=swap">
<style>
  :root {
    --ink: #222222;
    --navy: #0b2236;
    --teal-dark: #1d4a5a;
    --accent: #4a5db0;
    --phone: #6b63b5;
    --band: #1a93ae;
    --button: #99d6de;
    --footer: #282828;
    --white: #ffffff;
  }
  * { box-sizing: border-box; margin: 0; padding: 0; }
  html, body { width: 1167px; height: 1200px; overflow: hidden; background: var(--white); }
  body { position: relative; font-family: "Lato", sans-serif; color: var(--ink); }

  .site-header { position: absolute; top: 0; left: 0; width: 1167px; height: 104px; background: var(--white); z-index: 2; }
  .brand {
    position: absolute; left: 152px; top: 18px; width: 120px; height: 120px; border-radius: 50%;
    background: var(--white); box-shadow: 0 0 0 5px var(--white);
    display: flex; align-items: center; justify-content: center;
    font-family: "Lato", sans-serif; font-weight: 700; font-size: 17px; color: var(--navy);
    text-align: center; line-height: 1.1;
  }
  .phone { position: absolute; left: 863px; top: 16px; display: flex; align-items: center; gap: 12px; }
  .phone-icon { width: 31px; height: 31px; background: var(--phone); border-radius: 3px; display: flex; align-items: center; justify-content: center; }
  .phone-number { font-weight: 700; font-size: 19px; color: var(--phone); }
  .main-nav a {
    position: absolute; top: 74px; font-size: 12px; font-weight: 700; color: var(--ink);
    text-decoration: none; letter-spacing: 0.1px;
  }
  .main-nav a.is-current { color: var(--teal-dark); }
  .nav-marker { position: absolute; left: 867px; top: 98px; width: 64px; height: 6px; background: var(--teal-dark); }

  .hero {
    position: absolute; top: 104px; left: 0; width: 1167px; height: 258px;
    background: linear-gradient(100deg, #010d17 0%, #03223a 45%, #0a4a72 100%);
  }
  .hero-title { position: absolute; left: 140px; top: 100px; font-family: "Fira Sans", sans-serif; font-weight: 700; font-size: 43px; color: var(--white); }
  .hero-badge {
    position: absolute; left: 841px; top: 29px; width: 200px; height: 200px; border-radius: 50%;
    border: 4px solid #7fd8ea;
    background: radial-gradient(circle, #0e4f78 0%, #0a3d60 100%);
  }

  .content { position: absolute; top: 408px; left: 141px; width: 890px; font-size: 13.4px; line-height: 22.6px; }
  .content p { margin: 0; }
  .content h2 { font-family: "Fira Sans", sans-serif; font-weight: 500; font-size: 19.5px; color: var(--accent); line-height: 26px; }
  .intro { margin-bottom: 36px !important; }
  .content h2 { margin-bottom: 7px; }
  .section { margin-bottom: 21px; }

  .subscribe {
    position: absolute; top: 824px; left: 0; width: 1167px; height: 245px;
    background: linear-gradient(90deg, #1a9cb5 0%, #1b8fac 40%, #2a7aa0 55%, #1691af 75%, #1a9ab4 100%);
  }
  .subscribe h2 { position: absolute; top: 40px; width: 100%; text-align: center; font-family: "Fira Sans", sans-serif; font-weight: 500; font-size: 33px; color: var(--white); letter-spacing: 0.5px; }
  .field {
    position: absolute; top: 100px; height: 43px; width: 309px; background: var(--white);
    border: 0; font-family: "Lato", sans-serif; font-size: 12.5px; color: var(--ink); padding-left: 15px;
    display: flex; align-items: center;
  }
  .field-name { left: 268px; }
  .field-email { left: 590px; }
  .subscribe-button {
    position: absolute; top: 152px; left: 268px; width: 631px; height: 43px; background: var(--button);
    color: var(--white); font-weight: 700; font-size: 15.5px; display: flex; align-items: center; justify-content: center;
  }

  .site-footer { position: absolute; top: 1069px; left: 0; width: 1167px; height: 131px; background: var(--footer); color: var(--white); }
  .footer-nav { position: absolute; top: 23px; width: 100%; display: flex; justify-content: center; gap: 38px; }
  .footer-nav a { color: var(--white); text-decoration: none; font-weight: 700; font-size: 12.4px; }
  .copyright { position: absolute; top: 56px; width: 100%; text-align: center; font-size: 11px; }
  .social { position: absolute; top: 87px; width: 100%; display: flex; justify-content: center; gap: 17px; }
  .social span { width: 17px; height: 17px; border-radius: 50%; background: var(--white); }
</style>
</head>
<body>
  <header class="site-header">
    <div class="brand">Vela<br>Health</div>
    <div class="phone">
      <span class="phone-icon">
        <svg width="16" height="16" viewBox="0 0 24 24" aria-hidden="true"><path fill="#fff" d="M6.6 10.8a15.1 15.1 0 0 0 6.6 6.6l2.2-2.2c.3-.3.7-.4 1-.2 1.1.4 2.3.6 3.6.6.6 0 1 .4 1 1V20c0 .6-.4 1-1 1A17 17 0 0 1 3 4c0-.6.4-1 1-1h3.5c.6 0 1 .4 1 1 0 1.3.2 2.5.6 3.6.1.3 0 .7-.2 1z"/></svg>
      </span>
      <span class="phone-number">555-010-0199</span>
    </div>
    <nav class="main-nav">
      <a href="#" style="left:384px">HOME</a>
      <a href="#" style="left:461px">ABOUT US</a>
      <a href="#" style="left:563px">WHY VELA?</a>
      <a href="#" style="left:676px">SERVICE AREA</a>
      <a href="#" style="left:803px">OTHER</a>
      <a href="#" class="is-current" style="left:885px">FAQ</a>
      <a href="#" style="left:948px">CONTACT US</a>
    </nav>
    <span class="nav-marker"></span>
  </header>

  <section class="hero">
    <h1 class="hero-title">Other</h1>
    <div class="hero-badge" role="img" aria-label="Line illustration of a car with a medical caduceus on its roof"></div>
  </section>

  <main class="content">
    <p class="intro">Dr. Ray Castell &amp; Dr. Sam Porter founded Vela Health and are committed to their mission, vision and values.</p>
    <div class="section">
      <h2>Our Mission</h2>
      <p>To simplify our patients’ access to quality medical care and help our patients achieve optimal wellness.</p>
    </div>
    <div class="section" style="margin-top:32px">
      <h2>Our Vision:</h2>
      <p>Dr. Ray Castell &amp; Dr. Sam Porter founded Vela Health with the goal of getting back to basics: Bring the doctor to the patient. To make our vision happen, we will use the latest technologies and advancements in medical equipment, computer technology, geo- mapping and fleet management. We will stay on the cutting edge of personalized medical delivery and technologies.</p>
    </div>
    <div class="section">
      <h2>Our Values:</h2>
      <p>Treat patients like people, not numbers. Take time to care and know our patients. Be committed to helping our patients achieve optimal wellness through compassionately delivered, comfortable care.</p>
    </div>
  </main>

  <section class="subscribe">
    <h2>Subscribe</h2>
    <div class="field field-name">Enter Name</div>
    <div class="field field-email">Enter Email Address</div>
    <div class="subscribe-button">SUBSCRIBE NOW</div>
  </section>

  <footer class="site-footer">
    <nav class="footer-nav">
      <a href="#">HOME</a>
      <a href="#">ABOUT US</a>
      <a href="#">WHY VELA?</a>
      <a href="#">SERVICE AREA</a>
      <a href="#">OTHER</a>
      <a href="#">CONTACT US</a>
    </nav>
    <p class="copyright">Copyright &nbsp;© 2019.&nbsp; Company Name &nbsp;All Rights Reserved</p>
    <div class="social" aria-label="Social links">
      <span></span><span></span><span></span><span></span><span></span>
    </div>
  </footer>
</body>
</html>
```